Industry / Entity Type

Financial consultancy / advisers

Current site is: http://www.brightmoor-counsel.com

Looking for a complete overhaul of this site, we are after a clean modern look. Will require the ability to easily add, update and remove content, hence the WordPress design.
Example:
Add case studies
Industry documentation (downloadable brochures / flyers and such)

What we like from our current site is the colour the fonts and the logo (the city of London) we would like to have other city outlines (NYC and Tokyo, Hong Kong, Singapore).

The site will be used by our potential clients to get in contact and re-view the case studies, if possible would like to have a client login area where they can download our documents like NDA’s etc and T&C’s.

Task Outline

Create a Web Design (Coded - Design and coding required)
Designer must provide full implementation/coding depending on the platform chosen by the client (i.e. WordPress theme, HTML/CSS, bootstrap etc.)

Task Description

I need a full website built that must work on desktop and mobile. I can provide the London city skyline and the font file, which we have used. Some stock industrial photos will be required.

Requirements:

*Splash page
*What We Do
*How We do it
*Who Are We? To have the same information and links as the current site
*Why use us?
*Clients: To have the same information and links as the current site
*Partners: To have the same information and links as the current site
*Contact:

Target Market(s)

Financial institutions trading Equities, Futures, Options, Forex and Fixed Income.
Regulators, Exchanges, ECN’s
Buy side firms and Sell side firms

Industry/Entity Type

Financial

Coding

Coded - Design and coding required

Number of Pages Required

5+ page

Font styles to use
Sans Serif

Colors
f04a50

Requirements
Must have
• Splash page
• What We Do
• How We do it
• Who Are We? To have the same information and links as the current site
• Why use us?
• Clients: To have the same information and links as the current site
• Partners: To have the same information and links as the current site
• Contact:

```html
<!DOCTYPE html>
<html lang="en">
<head>
<meta charset="utf-8">
<title>Brightmoor Technology Counsel</title>
<link href="https://fonts.googleapis.com/css2?family=Poppins:wght@300;400;500;600;700&display=swap" rel="stylesheet">
<style>
:root{
  --red:#f04a50;
  --red-dark:#d9353b;
  --ink:#111;
  --text:#444;
  --muted:#9a9a9a;
  --soft:#f7f7f7;
  --white:#fff;
  --line:#e6e6e6;
}
*{box-sizing:border-box;margin:0;padding:0}
html,body{width:1200px;height:3371px;overflow:hidden}
body{font-family:'Poppins',sans-serif;color:var(--text);background:var(--white);position:relative}
section,header,nav,footer{position:absolute;left:0;width:1200px}
.site-header{top:0;height:146px;background:var(--white)}
.brand{position:absolute;left:202px;top:48px;display:flex;align-items:center;gap:12px}
.brand-mark{width:14px;height:14px;background:var(--ink)}
.brand-name{font-size:16px;font-weight:400;letter-spacing:3px;color:var(--ink);line-height:1.3;text-transform:uppercase}
.header-phone{position:absolute;left:808px;top:80px;font-size:15px;color:var(--ink);display:flex;align-items:center;gap:8px}
.main-nav{top:146px;height:70px;background:var(--red);display:flex;justify-content:center;align-items:center;gap:36px}
.main-nav a{color:var(--white);text-decoration:none;font-size:14px;font-weight:500}
.hero{top:216px;height:575px;text-align:center;color:var(--white);
  background:
    linear-gradient(180deg,rgba(20,30,50,.25),rgba(20,25,35,.35)),
    radial-gradient(ellipse 60% 35% at 50% 70%,rgba(214,160,90,.55),rgba(214,160,90,0) 70%),
    linear-gradient(180deg,#2f4a6e 0%,#4d6a8c 22%,#5f7690 34%,#6c6f78 48%,#7a6a5a 62%,#5a4c42 80%,#3a3330 100%)}
.hero h1{position:absolute;top:200px;width:100%;font-size:27px;font-weight:600;letter-spacing:1px}
.hero p{position:absolute;top:250px;width:100%;font-size:17px;font-weight:300}
.btn{display:inline-block;font-size:13px;font-weight:600;color:var(--white);text-decoration:none;text-transform:uppercase;text-align:center}
.hero .btn{position:absolute;left:526px;top:305px;width:148px;height:45px;line-height:45px;background:var(--red)}
.dots{position:absolute;top:487px;left:0;width:100%;display:flex;justify-content:center;gap:14px}
.dots span{width:9px;height:9px;border-radius:50%;background:var(--white)}
.dots span.active{background:var(--red)}
.section-title{position:absolute;width:100%;text-align:center;font-size:22px;font-weight:600;color:var(--ink)}
.section-sub{position:absolute;width:100%;text-align:center;font-size:13px;color:#c2c2c2;font-weight:300}
.logo-row{position:absolute;left:0;width:100%;display:flex;justify-content:center;align-items:center;gap:40px}
.logo-name{font-size:15px;font-weight:600;display:flex;align-items:center;gap:6px}
.logo-name i{display:inline-block;width:10px;height:10px;border-radius:50%;background:currentColor}
.clients{top:791px;height:265px;background:var(--soft)}
.clients .section-title{top:55px}
.clients .section-sub{top:97px}
.clients .logo-row{top:160px}
.cases{top:1056px;height:416px;background:var(--white)}
.cases .section-title{top:58px}
.case{position:absolute;top:128px;width:254px}
.case-img{width:254px;height:153px}
.case h3{margin-top:24px;font-size:14px;font-weight:600;color:var(--ink)}
.team{top:1472px;height:712px;background:var(--soft)}
.team .section-title{top:78px}
.member{position:absolute;left:200px;width:800px;height:173px}
.member-photo{position:absolute;left:0;top:0;width:186px;height:173px}
.member-body{position:absolute;left:213px;top:0;width:587px}
.member h3{font-size:18px;font-weight:600;color:var(--red)}
.member .role{font-size:13px;color:#777;margin-top:8px}
.member .bio{font-size:13px;line-height:23px;color:#333;margin-top:24px}
.arrow{position:absolute;top:395px}
.partners{top:2184px;height:294px;background:var(--white)}
.partners .section-title{top:62px}
.partners .section-sub{top:102px}
.partners .logo-row{top:176px}
.about{top:2478px;height:443px;color:var(--white);text-align:center;
  background:
    radial-gradient(ellipse 40% 60% at 65% 55%,rgba(150,30,35,.35),rgba(150,30,35,0) 70%),
    linear-gradient(135deg,#e24349 0%,#f04a50 45%,#d93c42 100%)}
.about .section-title{top:124px;color:var(--white)}
.about p{position:absolute;left:226px;top:186px;width:748px;font-size:13px;line-height:24px;font-weight:300}
.about .btn{position:absolute;left:523px;top:324px;width:151px;height:49px;line-height:45px;border:2px solid var(--white)}
.site-footer{top:2921px;height:450px;background:var(--white)}
.footer-brand{position:absolute;left:0;width:100%;top:56px;display:flex;justify-content:center;align-items:center;gap:10px}
.footer-brand .brand-name{font-size:12px;letter-spacing:2px}
.footer-brand .brand-mark{width:10px;height:10px}
.footer-col{position:absolute;top:155px;font-size:11px;color:#222;line-height:23px}
.footer-col h4{font-size:11px;font-weight:600;color:var(--red);margin-bottom:12px}
.footer-col ul{list-style:none}
.footer-col .privacy{line-height:19px;width:310px}
.footer-col .more{font-weight:600;margin-top:6px;display:block}
.bottom-bar{position:absolute;left:0;top:405px;width:1200px;height:45px;border-top:1px solid var(--line);font-size:9px;color:#333;text-align:center;line-height:45px}
.bottom-bar span{position:absolute;right:20px}
</style>
</head>
<body>
<header class="site-header">
  <div class="brand"><span class="brand-mark"></span><span class="brand-name">Brightmoor Technology<br>Counsel</span></div>
  <div class="header-phone">
    <svg width="14" height="14" viewBox="0 0 24 24"><path fill="#f04a50" d="M6.6 10.8a15.1 15.1 0 0 0 6.6 6.6l2.2-2.2a1 1 0 0 1 1-.25 11.4 11.4 0 0 0 3.6.6 1 1 0 0 1 1 1V20a1 1 0 0 1-1 1A17 17 0 0 1 3 4a1 1 0 0 1 1-1h3.5a1 1 0 0 1 1 1c0 1.25.2 2.45.6 3.6a1 1 0 0 1-.25 1z"/></svg>
    +44(0)20 7946 0183
  </div>
</header>

<nav class="main-nav">
  <a href="#">Home</a><a href="#">What We Do</a><a href="#">How We Do It</a><a href="#">Who Are We</a><a href="#">Why Use Us</a><a href="#">Clients</a><a href="#">Partners</a><a href="#">Contact</a>
</nav>

<section class="hero" role="img" aria-label="Night-time city skyline with harbour and illuminated towers under a blue dusk sky">
  <h1>TRAINING</h1>
  <p>Trading Technology for compliance and non techical staff</p>
  <a class="btn" href="#">Learn More</a>
  <div class="dots"><span class="active"></span><span></span><span></span><span></span></div>
</section>

<section class="clients">
  <h2 class="section-title">OUR CLIENTS</h2>
  <p class="section-sub">You will find an impressive list of clients that BTC have worked with.</p>
  <div class="logo-row">
    <span class="logo-name" style="color:#222">Norvale</span>
    <span class="logo-name" style="color:#333">Quillon Group</span>
    <span class="logo-name" style="color:#555">Tessary</span>
    <span class="logo-name" style="color:#666">Cellora</span>
    <span class="logo-name" style="color:#3a8a3a"><i></i>Brackwell</span>
    <span class="logo-name" style="color:#3b7fc4">Fernhold</span>
    <span class="logo-name" style="color:#1d5fa6">Solvane</span>
    <span class="logo-name" style="color:#2a4f8a">Merrin Systems</span>
  </div>
</section>

<section class="cases">
  <h2 class="section-title">CASE STUDIES</h2>
  <article class="case" style="left:200px"><div class="case-img" role="img" aria-label="Desk with laptop and printed financial charts" style="background:linear-gradient(135deg,#f4f5f7 0%,#d9dde3 45%,#b9c3cf 75%,#e7dcd2 100%)"></div><h3>Infrastructure Case Study</h3></article>
  <article class="case" style="left:474px"><div class="case-img" role="img" aria-label="Business meeting with documents on a table" style="background:linear-gradient(135deg,#6e6258 0%,#a8998a 40%,#d8d2c8 70%,#9b8f82 100%)"></div><h3>Tech-Startup-Case</h3></article>
  <article class="case" style="left:748px"><div class="case-img" role="img" aria-label="Businessman using a tablet in bright light" style="background:linear-gradient(135deg,#ffffff 0%,#eef0f2 40%,#b8c4d0 70%,#5f6f82 100%)"></div><h3>Tech-Due Diligence</h3></article>
</section>

<section class="team">
  <h2 class="section-title">TEAM</h2>
  <svg class="arrow" style="left:91px" width="16" height="26" viewBox="0 0 16 26"><path d="M13 2 3 13l10 11" fill="none" stroke="#111" stroke-width="3"/></svg>
  <svg class="arrow" style="left:1092px" width="16" height="26" viewBox="0 0 16 26"><path d="m3 2 10 11L3 24" fill="none" stroke="#111" stroke-width="3"/></svg>
  <article class="member" style="top:191px">
    <div class="member-photo" role="img" aria-label="Portrait photo of Owen Hartley" style="background:linear-gradient(180deg,#d9dde2 0%,#c9b3a3 45%,#9aa7b6 75%,#6f7f93 100%)"></div>
    <div class="member-body">
      <h3>Owen Hartley, CTO</h3>
      <p class="role">Senior Information Technology Executive</p>
      <p class="bio">Senior Information Technology Executive *Proof of invention can be supplied on request Private &amp; ConfidentialPage Owen Hartley was listed in the Top 3 CTO's in the financial technology space during 2013 for his forward thinking / innovation and integration skills in becoming part of one of the super - fast leading technology vendors</p>
    </div>
  </article>
  <article class="member" style="top:442px">
    <div class="member-photo" role="img" aria-label="Portrait photo of Simon Pryce" style="background:linear-gradient(180deg,#f2f0ec 0%,#d6bca8 40%,#8a7a6c 70%,#4a4440 100%)"></div>
    <div class="member-body">
      <h3>Simon Pryce, Former Chief Of Staff</h3>
      <p class="role">Senior Information Technology Executive</p>
      <p class="bio">Senior Information Technology Executive *Proof of invention can be supplied on request Private &amp; ConfidentialPage Simon Pryce was listed in the Top 3 CTO's in the financial technology space during 2013 for his forward thinking / innovation and integration skills in becoming part of one of the super - fast leading technology vendors</p>
    </div>
  </article>
</section>

<section class="partners">
  <h2 class="section-title">OUR PARTNERS</h2>
  <p class="section-sub">Impressive list of partners, working together, building solutions to drive business</p>
  <div class="logo-row">
    <span class="logo-name" style="color:#3a8a3a"><i></i>Brackwell</span>
    <span class="logo-name" style="color:#333">Quillon Group</span>
    <span class="logo-name" style="color:#e0262b">Ardent</span>
    <span class="logo-name" style="color:#1f2b4a;font-size:19px">Kestrix</span>
    <span class="logo-name" style="color:#2e7fc0">Pellow</span>
    <span class="logo-name" style="color:#2a9a4a">Tarnwell</span>
    <span class="logo-name" style="color:#555">Corvane</span>
  </div>
</section>

<section class="about" role="img" aria-label="Red-tinted image of a hand touching a financial growth chart">
  <h2 class="section-title">ABOUT US</h2>
  <p>Since founding Brightmoor Technology Counsel in 2014 we have dedicated ourselves to the provision of services. What differentiates us from other advisers or consultancies is a genuine motivation to see our clients succeed. Today's technology allows our clients to take their knowledge to the market in ways that previous generations could only dream of. That's why BTC is dedicated to seeing you choose the right technology</p>
  <a class="btn" href="#">Learn More</a>
</section>

<footer class="site-footer">
  <div class="footer-brand"><span class="brand-mark"></span><span class="brand-name">Brightmoor Technology Counsel</span></div>
  <div class="footer-col" style="left:220px">
    <h4>Quick Links</h4>
    <ul><li>Home</li><li>What We Do</li><li>How We Do It</li><li>Who Are We</li><li>Why Use Us</li><li>Clients</li><li>Partners</li><li>Contact</li></ul>
  </div>
  <div class="footer-col" style="left:438px">
    <h4>Contact Us</h4>
    <p>Suite 4 Larkfield Court,<br>Easthaven, Calder,<br>CL7 2PB</p>
    <p style="margin-top:16px">Company No 08815327<br>VAT No: 4471902</p>
  </div>
  <div class="footer-col" style="left:670px">
    <h4>Privacy</h4>
    <p class="privacy">BTC may receive names, e-mail addresses and other personally identifying information only when personally submitted by users through the optional BTC feedback feature. This information is not gathered by BTC without the user's knowledge, active permission and participation. The information submitted enables BTC to respond to user inquiries and suggestions. BTC respects the privacy</p>
    <a class="more">Read More</a>
  </div>
  <div class="bottom-bar">© 2017 Company Name | All Rights Reserved<span>CS</span></div>
</footer>
</body>
</html>
```